Talvo Pollution Mask Packaging

We need a packaging design for a pollution mask, image of mask attached. Have also attached a file with the exact measurements of the box.
There is also an example of a box attached, we would like a similar type design.
I have also attached the Logo, which should be fairly prominent in design.
The following blurb also needed:
Activated carbon dust mask.
99.999% Filtration
Instructions:
1: Place mask over mouth and nose.
2: Ensure aluminium bridge on top.
3: Adjust Tambix on back to desired tension.
4: Additional Filters sold separately.
Material Description
1: Filter 10% Ammonia
2: N99 Filter Cotton
3: CR Material 100% Neoprene
4: N Cloth 100% Nylon
Other font styles liked:
- RR Beaver

```html
<!DOCTYPE html>
<html lang="en">
<head>
<meta charset="UTF-8">
<title>Talvo Activated Carbon Dust Mask – Packaging</title>
<link rel="stylesheet" href="https://fonts.googleapis.com/css2?family=Oswald:wght@400;500;600;700&family=Montserrat:wght@400&display=swap">
<style>
  :root {
    --lime: #8cc21f;
    --ink: #1c1c1c;
    --charcoal: #363636;
    --grey-text: #8a8a8a;
    --paper: #e9ece4;
    --white: #ffffff;
  }
  * { margin: 0; padding: 0; box-sizing: border-box; }
  html, body { width: 1200px; height: 1200px; overflow: hidden; }
  body {
    background: var(--paper);
    font-family: "Oswald", sans-serif;
    position: relative;
  }
  .net { position: absolute; left: 40px; top: 230px; width: 1120px; height: 740px; display: flex; }
  .panel { position: relative; height: 100%; overflow: hidden; }
  .header { position: absolute; left: 0; top: 0; width: 100%; height: 200px; }
  .body { position: absolute; left: 0; top: 200px; width: 100%; height: 540px; }

  .front { width: 380px; }
  .side-a { width: 260px; }
  .back { width: 340px; }
  .side-b { width: 140px; }

  .dark { background: var(--ink); }
  .grey { background: var(--charcoal); }
  .green { background: var(--lime); }

  .hang-hole {
    position: absolute; width: 110px; height: 38px; border-radius: 19px;
    background: var(--white); top: 60px;
  }

  .title { line-height: 0.95; text-transform: uppercase; }
  .title .kicker { font-weight: 500; font-size: 26px; color: var(--lime); display: block; }
  .title .main { font-weight: 600; font-size: 50px; color: var(--lime); display: block; letter-spacing: -0.5px; }
  .title .spec { font-weight: 400; font-size: 24px; color: var(--white); display: block; margin-top: 4px; }

  .header-title { position: absolute; left: 24px; top: 52px; }

  .brand { display: flex; flex-direction: column; align-items: center; gap: 8px; }
  .brand .dot { border-radius: 50%; }
  .brand .name { font-weight: 700; text-transform: uppercase; letter-spacing: 2px; line-height: 1; }

  .front-brand { position: absolute; left: 30px; top: 70px; align-items: flex-start; }
  .front-brand .dot { width: 120px; height: 120px; background: var(--lime); margin-left: 30px; }
  .front-brand .name { font-size: 58px; color: var(--lime); }
  .front-title { position: absolute; left: 30px; top: 300px; }
  .front-title .spec { color: var(--grey-text); padding-bottom: 4px; border-bottom: 2px solid var(--lime); display: inline-block; }

  .side-header-brand { position: absolute; left: 0; right: 0; top: 48px; }
  .side-header-brand .dot { width: 64px; height: 64px; background: var(--ink); }
  .side-header-brand .name { font-size: 36px; color: var(--ink); }

  .back-header-brand { position: absolute; right: 40px; top: 52px; }
  .back-header-brand .dot { width: 54px; height: 54px; background: var(--lime); }
  .back-header-brand .name { font-size: 32px; color: var(--lime); }

  .activities { position: absolute; left: 14px; top: 20px; width: 100px; }
  .activities .lead { font-size: 15px; font-weight: 500; color: var(--ink); line-height: 1; text-transform: uppercase; white-space: nowrap; }
  .activities .lead b { display: block; font-size: 22px; font-weight: 600; }
  .activity-icon { width: 60px; height: 60px; background: var(--ink); border-radius: 6px; margin: 40px 0 0 18px; opacity: 0.85; }

  .side-column { position: absolute; top: 0; bottom: 0; left: 115px; width: 145px; }

  .vertical-block { position: absolute; top: 130px; display: flex; gap: 4px; }
  .vertical-block span { writing-mode: vertical-rl; text-transform: uppercase; color: var(--ink); line-height: 1; white-space: nowrap; }
  .vertical-block .big { font-size: 58px; font-weight: 600; }
  .vertical-block .small { font-size: 28px; font-weight: 500; padding-top: 6px; }

  .side-brand { position: absolute; top: 20px; left: 0; right: 0; }
  .side-brand .dot { width: 58px; height: 58px; background: var(--ink); }
  .side-brand .name { font-size: 28px; color: var(--ink); }

  .filtration { position: absolute; bottom: 18px; left: 0; right: 0; font-size: 28px; color: var(--ink); text-transform: uppercase; line-height: 1; text-align: center; font-weight: 500; }
  .filtration small { display: block; font-size: 22px; }

  .photo {
    position: absolute; left: 0; top: 0; width: 100%; height: 340px;
    background: radial-gradient(ellipse at 40% 40%, #c6e37a 0%, #7aa52a 45%, #36491a 100%);
  }
  .materials { position: absolute; left: 36px; top: 380px; font-family: "Montserrat", sans-serif; color: #bdbdbd; font-size: 15px; line-height: 1.45; }
</style>
</head>
<body>
  <main class="net">
    <section class="panel front">
      <div class="header dark">
        <h2 class="title header-title">
          <span class="kicker">Activated Carbon</span>
          <span class="main">Dust Mask</span>
          <span class="spec">99.999% Filtration</span>
        </h2>
        <div class="hang-hole" style="left:262px"></div>
      </div>
      <div class="body grey">
        <div class="brand front-brand"><span class="dot"></span><span class="name">Talvo</span></div>
        <h1 class="title front-title">
          <span class="kicker">Activated Carbon</span>
          <span class="main">Dust Mask</span>
          <span class="spec">99.999% Filtration</span>
        </h1>
      </div>
    </section>

    <section class="panel side-a">
      <div class="header green">
        <div class="brand side-header-brand"><span class="dot"></span><span class="name">Talvo</span></div>
      </div>
      <div class="body green">
        <div class="activities">
          <p class="lead">Great for all <b>Outdoor</b><b>Activities</b></p>
          <div class="activity-icon" role="img" aria-label="Cycling icon"></div>
          <div class="activity-icon" role="img" aria-label="Climbing icon"></div>
          <div class="activity-icon" role="img" aria-label="Kayaking icon"></div>
          <div class="activity-icon" role="img" aria-label="Hiking icon"></div>
        </div>
        <div class="side-column">
          <div class="brand side-brand"><span class="dot"></span><span class="name">Talvo</span></div>
          <div class="vertical-block" style="left:22px">
            <span class="big">Dust Mask</span>
            <span class="small">Activated Carbon</span>
          </div>
          <p class="filtration">99.999%<small>Filtration</small></p>
        </div>
      </div>
    </section>

    <section class="panel back">
      <div class="header dark">
        <div class="hang-hole" style="left:40px"></div>
        <div class="brand back-header-brand"><span class="dot"></span><span class="name">Talvo</span></div>
      </div>
      <div class="body dark">
        <div class="photo" role="img" aria-label="Green-toned photo of a mountain biker riding over a mossy rock"></div>
        <div class="materials">
          <p>Material Description</p>
          <p>1: Filter 10% Ammonia</p>
          <p>2: N99 Filter Cotton</p>
          <p>3: CR Material 100% Neoprene</p>
          <p>4: N Cloth 100% Nylon</p>
        </div>
      </div>
    </section>

    <section class="panel side-b">
      <div class="header dark"></div>
      <div class="body green">
        <div class="brand side-brand"><span class="dot"></span><span class="name">Talvo</span></div>
        <div class="vertical-block" style="left:20px">
          <span class="big">Dust Mask</span>
          <span class="small">Activated Carbon</span>
        </div>
        <p class="filtration">99.999%<small>Filtration</small></p>
      </div>
    </section>
  </main>
</body>
</html>
```